Business Card Design

I'm a commercial general contractor remodel offices, hotels, health clubs and stores mostly San Francisco and the peninsula
the file I down loaded is kind of what I want I like the I beam with my company name in it, that would be fine with me but if you have better Idea will look at it you never know, I'm decided to give in and change my company name to how every one knows me, I have been in business since 1991, I like the I beam logo I included one of my old card from my old company for reference for you.

BROCK CONSTRUCTION (is my company name)
Warren Pelkey contractor, LIc 514387
3148 Larkspur Row, San Bruno, California 94071
mobile, (415) 736-4052
phone (650) 514-2087
Fax, (650) 514-2088
email, brock@brockconstruction.example

```html
<!DOCTYPE html>
<html lang="en">
<head>
<meta charset="utf-8">
<title>Brock Construction — Business Card</title>
<link rel="stylesheet" href="https://fonts.googleapis.com/css2?family=Source+Sans+3:wght@400;600;700&display=swap">
<style>
  :root {
    --page: #d9d6d2;
    --card-top: #f1f2f3;
    --card-bottom: #e3e5e7;
    --navy: #1d4f86;
    --blue: #2a78c4;
    --ink: #3a3a3a;
    --band-dark: #1e1e1e;
    --web: #c9b8a8;
    --rule: #9a9a9a;
  }
  * { margin: 0; padding: 0; box-sizing: border-box; }
  html, body { width: 1200px; height: 970px; overflow: hidden; }
  body {
    background: var(--page);
    font-family: "Source Sans 3", "Myriad Pro", Arial, sans-serif;
    position: relative;
  }
  .card {
    position: absolute;
    left: 60px; top: 185px;
    width: 1080px; height: 600px;
    border-radius: 22px;
    overflow: hidden;
    background: linear-gradient(180deg, var(--card-top), var(--card-bottom));
    box-shadow: 0 10px 30px rgba(0,0,0,.18);
  }
  .contact { position: absolute; left: 72px; top: 98px; color: var(--ink); }
  .contact__name { font-size: 33px; font-weight: 600; color: var(--navy); line-height: 1.1; }
  .contact__title { font-size: 26px; margin-top: 4px; }
  .contact__address { margin-top: 58px; font-size: 25px; line-height: 36px; }
  .contact__lines { margin-top: 10px; list-style: none; font-size: 25px; line-height: 36px; }
  .contact__label { color: var(--blue); display: inline-block; width: 34px; }
  .divider {
    position: absolute; left: 558px; top: 140px;
    width: 1px; height: 310px; background: var(--rule); opacity: .6;
  }
  .badge {
    position: absolute; right: 78px; top: 66px;
    text-align: right;
  }
  .badge__name {
    font-size: 42px; font-weight: 700; color: var(--blue); letter-spacing: 1px;
  }
  .badge__lic { font-size: 19px; color: var(--ink); margin-top: 4px; }
  .brand {
    position: absolute; left: 590px; top: 235px; width: 440px;
    text-align: center; color: var(--blue); font-weight: 700;
  }
  .brand__main { font-size: 104px; line-height: 1; letter-spacing: 6px; }
  .brand__sub { font-size: 31px; letter-spacing: 2px; margin-top: 6px; }
  .band { position: absolute; left: 0; bottom: 0; width: 1080px; height: 86px; }
  .website {
    position: absolute; left: 72px; bottom: 28px;
    font-size: 25px; color: var(--web); letter-spacing: .3px;
  }
</style>
</head>
<body>
  <article class="card">
    <section class="contact">
      <h1 class="contact__name">Warren Pelkey</h1>
      <p class="contact__title">President</p>
      <p class="contact__address">3148 Larkspur Row<br>Alder Bay,Ca 94071</p>
      <ul class="contact__lines">
        <li><span class="contact__label">T:</span>650 514 - 2087</li>
        <li><span class="contact__label">C:</span>415 736 - 4052</li>
        <li><span class="contact__label">F:</span>650 514 - 2088</li>
        <li><span class="contact__label">E:</span>brock@brockconstruction.example</li>
      </ul>
    </section>

    <div class="divider"></div>

    <div class="badge">
      <div class="badge__name">BC, INC.</div>
      <div class="badge__lic">Lic#514387</div>
    </div>

    <div class="brand">
      <div class="brand__main">BROCK</div>
      <div class="brand__sub">CONSTRUCTION</div>
    </div>

    <svg class="band" viewBox="0 0 1080 86" preserveAspectRatio="none" aria-hidden="true">
      <path d="M0 0 H520 C560 0 565 30 610 30 H1080 V86 H0 Z" fill="var(--band-dark)"/>
      <path d="M560 0 H1080 V30 H610 C590 30 580 4 560 0 Z" fill="var(--blue)"/>
      <path d="M520 0 C560 0 565 30 610 30 H1080" fill="none" stroke="#8d8d8d" stroke-width="2"/>
    </svg>
    <p class="website">www.brockconstruction.example</p>
  </article>
</body>
</html>
```